Business Card Design Project

I require a business card with the following information on them for various different people;
name
m:
f:
e:
I have a logo already and will attached that. We are in the construction industry. I require something clean and simple but eye catching at the same time. You can use another colour with our logo if you like and you can style the logo as well if you wish. I am open.
Also it needs to be front and back design.
Industry/Entity Type
Construction
Requirements
Must have
- Logo, name, mobile, fax and email address.
Front and back design

```html
<!DOCTYPE html>
<html lang="en">
<head>
<meta charset="utf-8">
<title>Northgate Building Group – Business Card</title>
<link rel="stylesheet" href="https://fonts.googleapis.com/css2?family=Questrial&family=Arimo:wght@400&display=swap">
<style>
  :root {
    --stage: #141414;
    --card: #ffffff;
    --green: #7dc142;
    --green-light: #9fd45a;
    --green-dark: #0f4a2a;
    --band-deep: #1e5a1c;
    --grey: #b8b8b8;
    --grey-faint: #ececec;
    --ink: #111111;
    --brand-font: "Questrial", "Century Gothic", sans-serif;
    --body-font: "Arimo", Arial, sans-serif;
  }
  * { box-sizing: border-box; margin: 0; padding: 0; }
  html, body { width: 1200px; height: 900px; overflow: hidden; background: var(--stage); }
  .canvas {
    width: 1200px; height: 900px;
    display: flex; flex-direction: column; align-items: center; justify-content: center;
    gap: 40px;
  }
  .card {
    position: relative;
    width: 620px; height: 355px;
    background: var(--card);
    overflow: hidden;
    box-shadow: 0 6px 18px rgba(0,0,0,.45);
  }
  .card-art { position: absolute; inset: 0; width: 620px; height: 355px; }

  .brand {
    position: absolute;
    display: flex; align-items: center; gap: 12px;
    font-family: var(--brand-font);
    color: var(--green);
    white-space: nowrap;
  }
  .brand-square { width: 34px; height: 34px; background: var(--green); flex: none; }
  .brand-name { font-size: 34px; line-height: 1.05; letter-spacing: .5px; }
  .front .brand { left: 150px; top: 48px; }
  .back .brand { left: 50%; top: 80px; transform: translateX(-50%); }
  .back .brand-name { font-size: 40px; }
  .back .brand-square { width: 40px; height: 40px; }

  .holder {
    position: absolute; left: 36px; top: 172px;
    font-family: var(--brand-font);
    font-size: 28px; color: var(--green);
  }
  .holder-rule {
    position: absolute; left: 22px; top: 208px;
    width: 300px; height: 3px; background: var(--green-dark);
  }
  .contacts {
    position: absolute; left: 48px; top: 220px;
    display: grid; grid-template-columns: 170px auto; row-gap: 8px; column-gap: 10px;
    font-family: var(--body-font); font-size: 15px; color: var(--ink);
  }
  .contact { display: flex; align-items: center; gap: 9px; white-space: nowrap; }
  .contact svg { width: 16px; height: 16px; flex: none; }
</style>
</head>
<body>
<main class="canvas">

  <section class="card front" aria-label="Card front">
    <svg class="card-art" viewBox="0 0 620 355" aria-hidden="true">
      <rect class="faint-mark" x="470" y="40" width="110" height="110" fill="var(--grey-faint)"/>
      <polygon class="band-grey" points="486,272 620,272 620,280 480,280" fill="var(--grey)"/>
      <polygon class="band-light" points="466,283 620,283 620,290 460,290" fill="var(--green)"/>
      <polygon class="band-dark" points="0,300 430,300 446,292 620,292 620,335 0,335" fill="var(--green-dark)"/>
      <polygon class="band-light-low" points="0,294 434,294 426,298 0,298" fill="var(--green)"/>
    </svg>

    <div class="brand">
      <span class="brand-square"></span>
      <span class="brand-name">Northgate<br>Building Group</span>
    </div>

    <div class="holder">Marcus Hale</div>
    <div class="holder-rule"></div>

    <div class="contacts">
      <div class="contact phone">
        <svg viewBox="0 0 16 16"><path d="M3 1l3 1 1 3-2 1.5c.8 1.8 2.2 3.2 4 4L10.5 9l3 1 1 3-2 2C6 14.5 1.5 10 1 3z" fill="var(--green)"/></svg>
        <span>03 9000 4812</span>
      </div>
      <div class="contact mobile">
        <svg viewBox="0 0 16 16"><rect x="4" y="1" width="8" height="14" rx="1.5" fill="var(--green)"/><rect x="5.5" y="3" width="5" height="6" fill="#fff"/></svg>
        <span>0400 218 563</span>
      </div>
      <div class="contact fax">
        <svg viewBox="0 0 16 16"><rect x="4" y="1" width="8" height="5" fill="var(--green)"/><rect x="1" y="6" width="14" height="6" rx="1" fill="var(--green)"/><rect x="4" y="10" width="8" height="5" fill="#fff" stroke="var(--green)"/></svg>
        <span>03 9000 5937</span>
      </div>
      <div class="contact email">
        <svg viewBox="0 0 16 16"><rect x="1" y="3.5" width="14" height="9" fill="none" stroke="var(--green)" stroke-width="1.4"/><path d="M1 3.5l7 5 7-5" fill="none" stroke="var(--green)" stroke-width="1.4"/></svg>
        <span>marcus@northgatebuild.com.au</span>
      </div>
    </div>
  </section>

  <section class="card back" aria-label="Card back">
    <svg class="card-art" viewBox="0 0 620 355" aria-hidden="true">
      <defs>
        <linearGradient id="backBand" x1="0" x2="1" y1="0" y2="0">
          <stop offset="0" stop-color="var(--band-deep)"/>
          <stop offset=".3" stop-color="var(--green)"/>
          <stop offset=".7" stop-color="var(--green)"/>
          <stop offset="1" stop-color="var(--band-deep)"/>
        </linearGradient>
      </defs>
      <rect class="rule-black" x="0" y="236" width="620" height="4" fill="var(--ink)"/>
      <rect class="band-green" x="0" y="246" width="620" height="50" fill="url(#backBand)"/>
    </svg>

    <div class="brand">
      <span class="brand-square"></span>
      <span class="brand-name">Northgate<br>Building Group</span>
    </div>
  </section>

</main>
</body>
</html>
```